Institute for Hip Wellness at Brightwater
business card and stationary
Institute for Hip Wellness at Brightwater -
Creative Brief
Professional
Gordon T. Sleet, MD
482 Fennick Lane, Suite 207 Annapolis, MD 21409
gtsleet82@brightmailbox.net
www.hipwellclinic-demo.com
Use new logo Comprehensive Gynecologic Care with Specialization in Chronic Pain Disorders and Minimally Invasive Surgery
Appointment Date and Time: Mon. _______ Tue _____ Wed ______ Thurs_______ Fri_______ _______ AM _______ PM

```html
<!DOCTYPE html>
<html lang="en">
<head>
<meta charset="utf-8">
<title>Institute for Hip Wellness at Brightwater – Stationery</title>
<link href="https://fonts.googleapis.com/css2?family=Open+Sans:wght@400;600&display=swap" rel="stylesheet">
<style>
:root{
  --bg:#2e2e2e;
  --paper:#ffffff;
  --plum:#a4649c;
  --plum-light:#cfa3c9;
  --slate:#6b6b6b;
  --ink:#555555;
  --faint:#efe6ee;
}
*{box-sizing:border-box;margin:0;padding:0}
html,body{width:1200px;height:338px;overflow:hidden;background:var(--bg);font-family:"Open Sans",sans-serif}
.canvas{position:relative;width:1200px;height:338px}
.sheet{position:absolute;background:var(--paper);overflow:hidden;box-shadow:0 2px 6px rgba(0,0,0,.45)}
.swoosh{position:absolute;top:0;right:0}
.brand{position:absolute;display:flex;align-items:center;gap:3px;color:var(--plum);font-weight:600;line-height:1.1}
.brand .dot{flex:none;border-radius:50%;background:var(--plum)}
.brand .name{max-width:70px}
.watermark{position:absolute;border-radius:50%;background:var(--faint)}
.small-print{position:absolute;color:var(--ink);font-size:3px;line-height:1.4}

/* business cards */
.card{width:108px;height:56px}
.card--front{left:12px;top:174px}
.card--back{left:12px;top:238px}
.card--front .brand{left:10px;top:18px;font-size:5px}
.card--front .brand .dot{width:8px;height:8px}
.card--back .holder{position:absolute;left:8px;top:10px;color:var(--plum);font-size:4.5px;font-weight:600}
.card--back .small-print{left:8px;top:20px}
.card--back .bar{position:absolute;left:0;bottom:0;width:100%;height:4px;background:var(--plum)}

/* letterheads */
.letterhead{top:14px;width:230px;height:315px}
.letterhead--one{left:140px}
.letterhead--two{left:390px}
.letterhead .brand{left:16px;top:16px;font-size:6px}
.letterhead .brand .dot{width:11px;height:11px}
.letterhead .watermark{width:90px;height:90px;left:70px;top:195px}
.letterhead .small-print{left:0;right:0;bottom:8px;text-align:center}

/* envelopes */
.envelope{left:629px;width:223px;height:100px}
.envelope--one{top:110px}
.envelope--two{top:226px}
.envelope .brand{left:10px;top:10px;font-size:5px}
.envelope .brand .dot{width:9px;height:9px}
.envelope .small-print{left:10px;top:34px}

/* envelope backs */
.env-back{left:907px;width:281px;height:96px}
.env-back--plum{top:12px}
.env-back--slate{top:113px}
.env-back--white{top:214px}
.env-back svg{position:absolute;inset:0}
.env-back .seal{position:absolute;left:135px;width:11px;height:11px;border-radius:50%;background:var(--paper)}
.env-back--plum .seal{top:30px}
.env-back--slate .seal{top:30px}
.env-back--white .seal{top:30px;background:var(--plum)}
</style>
</head>
<body>
<main class="canvas">

  <section class="sheet card card--front">
    <svg class="swoosh" width="50" height="56" viewBox="0 0 50 56"><path d="M50 0H20C34 12 42 30 50 56Z" fill="var(--plum)"/></svg>
    <div class="brand"><span class="dot"></span><span class="name">Institute for Hip Wellness at Brightwater</span></div>
  </section>

  <section class="sheet card card--back">
    <p class="holder">Gordon T. Sleet, MD</p>
    <p class="small-print">482 Fennick Lane, Suite 207<br>Annapolis, MD 21409<br>gtsleet82@brightmailbox.net<br>www.hipwellclinic-demo.com</p>
    <div class="bar"></div>
  </section>

  <section class="sheet letterhead letterhead--one">
    <svg class="swoosh" width="110" height="160" viewBox="0 0 110 160"><path d="M110 0H40C80 30 100 90 110 160Z" fill="var(--plum)"/><path d="M110 0H70C95 30 106 80 110 120Z" fill="var(--plum-light)" opacity=".6"/></svg>
    <div class="brand"><span class="dot"></span><span class="name">Institute for Hip Wellness at Brightwater</span></div>
    <div class="watermark" role="img" aria-label="Faint brand emblem"></div>
    <p class="small-print">482 Fennick Lane, Suite 207 Annapolis, MD 21409 · gtsleet82@brightmailbox.net · www.hipwellclinic-demo.com</p>
  </section>

  <section class="sheet letterhead letterhead--two">
    <svg class="swoosh" width="110" height="160" viewBox="0 0 110 160"><path d="M110 0H40C80 30 100 90 110 160Z" fill="var(--plum)"/><path d="M110 0H70C95 30 106 80 110 120Z" fill="var(--plum-light)" opacity=".6"/></svg>
    <div class="brand"><span class="dot"></span><span class="name">Institute for Hip Wellness at Brightwater</span></div>
    <div class="watermark" role="img" aria-label="Faint brand emblem"></div>
    <p class="small-print">482 Fennick Lane, Suite 207 Annapolis, MD 21409 · gtsleet82@brightmailbox.net · www.hipwellclinic-demo.com</p>
  </section>

  <section class="sheet envelope envelope--one">
    <svg class="swoosh" width="70" height="100" viewBox="0 0 70 100"><path d="M70 0H25C48 20 62 60 70 100Z" fill="var(--plum)"/></svg>
    <div class="brand"><span class="dot"></span><span class="name">Institute for Hip Wellness at Brightwater</span></div>
    <p class="small-print">482 Fennick Lane, Suite 207<br>Annapolis, MD 21409</p>
  </section>

  <section class="sheet envelope envelope--two">
    <svg class="swoosh" width="70" height="100" viewBox="0 0 70 100"><path d="M70 0H25C48 20 62 60 70 100Z" fill="var(--plum)"/></svg>
    <div class="brand"><span class="dot"></span><span class="name">Institute for Hip Wellness at Brightwater</span></div>
    <p class="small-print">482 Fennick Lane, Suite 207<br>Annapolis, MD 21409</p>
  </section>

  <section class="sheet env-back env-back--plum">
    <svg viewBox="0 0 281 96" preserveAspectRatio="none"><path d="M0 0H281L150 50Q140 54 131 50Z" fill="var(--plum)"/></svg>
    <span class="seal"></span>
  </section>

  <section class="sheet env-back env-back--slate">
    <svg viewBox="0 0 281 96" preserveAspectRatio="none"><path d="M0 0H281L150 50Q140 54 131 50Z" fill="var(--slate)"/></svg>
    <span class="seal"></span>
  </section>

  <section class="sheet env-back env-back--white">
    <svg viewBox="0 0 281 96" preserveAspectRatio="none"><path d="M0 0H281L150 50Q140 54 131 50Z" fill="#fafafa" stroke="#dddddd" stroke-width=".6"/></svg>
    <span class="seal"></span>
  </section>

</main>
</body>
</html>
```